Business card design needed

I need a business card design for a new online retail business based in Australia. I am unsure of the exact content of what I will be selling but it will be probably women's clothing, accessories, gym wear, gifts and maybe homeware linen. I am wanting a classy design that portrays the image of class/style/upmarket.

Target Market(s)

predominantely women - 20-50 age group

Industry/Entity Type

Retail

Contact Information for Business Card

Quietly Golden
Renata Calloway
Director
ABN 73418250964
17 Harrow Crescent Linfield Park NSW 2391
ph: +61 427 905 184
sales@quietlygolden.com.au

Logo Text

I am open for suggestions here

Requirements
Must have
• The design must be both sides of the card

```html
<!DOCTYPE html>
<html lang="en">
<head>
<meta charset="utf-8">
<title>Quietly Golden – Business Card</title>
<link rel="stylesheet" href="https://fonts.googleapis.com/css2?family=Arimo:wght@400;700&display=swap">
<style>
  :root {
    --ink: #231f20;
    --paper: #ffffff;
    --orange: #f08c2e;
    --rose: #cc5c78;
    --purple: #a2389d;
    --text-light: #f2f2f2;
    --accent: #f39a2b;
  }
  html, body {
    margin: 0;
    padding: 0;
    width: 1200px;
    height: 900px;
    overflow: hidden;
    background: var(--paper);
    font-family: "Arimo", Arial, sans-serif;
  }
  .canvas {
    position: relative;
    width: 1200px;
    height: 900px;
    background: var(--paper);
  }
  .card {
    position: absolute;
    left: 320px;
    width: 560px;
    height: 320px;
    overflow: hidden;
    box-shadow: 0 4px 14px rgba(0,0,0,0.18);
  }
  .card--front { top: 110px; }
  .card--back  { top: 470px; background: var(--ink); }

  .card__art { position: absolute; inset: 0; }

  .brand {
    position: absolute;
    display: flex;
    align-items: center;
    gap: 12px;
    white-space: nowrap;
  }
  .brand__dot {
    border-radius: 50%;
    flex: none;
  }
  .card--front .brand {
    left: 50%;
    top: 50%;
    transform: translate(-50%, -50%);
  }
  .card--front .brand__dot { width: 22px; height: 22px; background: var(--orange); }
  .card--front .brand__name {
    font-size: 38px;
    font-weight: 700;
    color: var(--purple);
  }

  .back__strip {
    position: absolute;
    left: 0; top: 0; bottom: 0;
    width: 150px;
    background: linear-gradient(180deg, var(--orange) 0%, var(--rose) 42%, var(--purple) 82%);
  }
  .card--back .brand {
    left: 0;
    width: 150px;
    bottom: 30px;
    justify-content: center;
    gap: 6px;
  }
  .card--back .brand__dot { width: 10px; height: 10px; background: var(--paper); }
  .card--back .brand__name {
    font-size: 16px;
    font-weight: 700;
    color: var(--paper);
  }

  .contact {
    position: absolute;
    left: 176px;
    top: 0;
    bottom: 0;
    right: 20px;
    color: var(--text-light);
  }
  .contact__name {
    position: absolute;
    top: 96px;
    margin: 0;
    font-size: 22px;
    font-weight: 400;
    color: var(--accent);
  }
  .contact__role {
    position: absolute;
    top: 128px;
    margin: 0;
    font-size: 13px;
  }
  .contact__address {
    position: absolute;
    top: 196px;
    margin: 0;
    font-size: 13px;
    line-height: 1.35;
    font-style: normal;
  }
  .contact__lines {
    position: absolute;
    top: 250px;
    margin: 0;
    padding: 0;
    list-style: none;
    font-size: 13px;
    line-height: 1.45;
  }
  .contact__lines li { display: flex; align-items: center; gap: 7px; }
  .icon { width: 11px; height: 11px; flex: none; fill: var(--accent); }
</style>
</head>
<body>
<main class="canvas">

  <section class="card card--front" aria-label="Business card front">
    <svg class="card__art" viewBox="0 0 560 320" preserveAspectRatio="none" aria-hidden="true">
      <defs>
        <linearGradient id="frontGlow" x1="0" y1="1" x2="1" y2="0">
          <stop offset="0" stop-color="#cc5c78"/>
          <stop offset="0.5" stop-color="#e0735a"/>
          <stop offset="1" stop-color="#f08c2e"/>
        </linearGradient>
      </defs>
      <rect width="560" height="320" fill="url(#frontGlow)"/>
      <path d="M0,0 H430 C520,70 560,190 560,320 H140 C50,260 0,140 0,0 Z"
            fill="#231f20" stroke="#ffffff" stroke-width="9"/>
    </svg>
    <div class="brand">
      <span class="brand__dot"></span>
      <span class="brand__name">Quietly Golden</span>
    </div>
  </section>

  <section class="card card--back" aria-label="Business card back">
    <div class="back__strip"></div>
    <div class="brand">
      <span class="brand__dot"></span>
      <span class="brand__name">Quietly Golden</span>
    </div>
    <div class="contact">
      <h1 class="contact__name">Renata Calloway</h1>
      <p class="contact__role">Director</p>
      <address class="contact__address">ABN 73418250964 17 Harrow Crescent<br>Linfield Park NSW 2391</address>
      <ul class="contact__lines">
        <li>
          <svg class="icon" viewBox="0 0 24 24" aria-hidden="true"><path d="M6.6 10.8c1.4 2.8 3.8 5.1 6.6 6.6l2.2-2.2c.3-.3.7-.4 1-.2 1.1.4 2.3.6 3.6.6.6 0 1 .4 1 1V20c0 .6-.4 1-1 1C10.6 21 3 13.4 3 4c0-.6.4-1 1-1h3.5c.6 0 1 .4 1 1 0 1.3.2 2.5.6 3.6.1.3 0 .7-.2 1l-2.3 2.2z"/></svg>
          <span>+61 427 905 184</span>
        </li>
        <li>
          <svg class="icon" viewBox="0 0 24 24" aria-hidden="true"><path d="M2 5h20v14H2z M3 6l9 7 9-7" fill="var(--accent)" stroke="#231f20" stroke-width="1.5"/></svg>
          <span>sales@quietlygolden.com.au</span>
        </li>
      </ul>
    </div>
  </section>

</main>
</body>
</html>
```